Veldmark Supplies Business Card

Professional business card that stand out to our potential customers. Front and back with clean modern design

Industry/Entity Type

Oil and gas

Contact Information for Business Card

Name, address, website , office phone and cell number

Requirements
Must have
• Editable files for each employee

```html
<!DOCTYPE html>
<html lang="en">
<head>
<meta charset="utf-8">
<title>Veldmark Supplies – Business Card</title>
<link rel="stylesheet" href="https://fonts.googleapis.com/css2?family=Archivo+Black&family=Exo+2:wght@400;500;700;800&display=swap">
<style>
  :root {
    --stage: #3a3a3c;
    --card: #2b2b2c;
    --card-back: #1d1d1e;
    --red: #ff0000;
    --cyan: #05b4d8;
    --white: #f2f2f2;
    --rule: #d9d9d9;
  }
  * { box-sizing: border-box; margin: 0; padding: 0; }
  html, body { width: 1200px; height: 694px; overflow: hidden; }
  body {
    background: var(--stage);
    font-family: "Exo 2", sans-serif;
    position: relative;
  }
  .card {
    position: absolute;
    top: 187px;
    width: 560px;
    height: 320px;
    border-radius: 22px;
    overflow: hidden;
    box-shadow: 0 10px 28px rgba(0,0,0,.45);
  }
  /* Back side */
  .card-back { left: 26px; background: var(--card-back); }
  .back-texture {
    position: absolute; inset: 0;
    background: radial-gradient(ellipse at 55% 45%, #4a4a4b 0%, #2a2a2b 45%, #151516 100%);
  }
  .back-brand {
    position: absolute; top: 50%; left: 50%;
    transform: translate(-50%, -50%);
    display: flex; align-items: center; gap: 10px;
  }
  .brand-square { width: 18px; height: 18px; background: var(--cyan); }
  .brand-name {
    font-weight: 800; font-size: 22px; color: var(--red);
    letter-spacing: .5px; white-space: nowrap;
  }
  /* Front side */
  .card-front { left: 614px; background: var(--card); }
  .front-brand {
    position: absolute; top: 44px; right: 34px;
    display: flex; align-items: center; gap: 10px;
  }
  .front-brand .brand-square { width: 40px; height: 40px; background: var(--red); }
  .front-brand .brand-name { font-size: 20px; color: var(--white); text-transform: uppercase; }
  .person { position: absolute; left: 30px; top: 152px; }
  .person-name {
    font-family: "Archivo Black", sans-serif;
    font-size: 29px; color: var(--red); line-height: 1;
  }
  .person-role { font-size: 16px; color: var(--cyan); margin-top: 6px; }
  .divider {
    position: absolute; left: 30px; right: 30px; top: 210px;
    height: 1px; background: var(--rule);
  }
  .contacts { position: absolute; left: 30px; top: 222px; list-style: none; }
  .contacts li {
    display: flex; align-items: center; gap: 10px;
    font-size: 15px; color: var(--white); height: 21px;
  }
  .contacts svg { width: 14px; height: 14px; fill: var(--cyan); }
  .address {
    position: absolute; right: 30px; top: 222px;
    text-align: right; font-size: 15px; color: var(--white); line-height: 21px;
  }
  .stripes { position: absolute; left: 0; bottom: 0; width: 560px; height: 40px; }
  .website {
    position: absolute; right: 30px; bottom: 6px;
    font-size: 14px; color: var(--white);
  }
</style>
</head>
<body>

<section class="card card-back" aria-label="Card back">
  <div class="back-texture" role="img" aria-label="Tonal embossed pattern repeating the company mark across the card"></div>
  <div class="back-brand">
    <span class="brand-square"></span>
    <span class="brand-name">Veldmark Supplies</span>
  </div>
</section>

<section class="card card-front" aria-label="Card front">
  <div class="front-brand">
    <span class="brand-square"></span>
    <span class="brand-name">Veldmark Supplies</span>
  </div>

  <div class="person">
    <p class="person-name">Corwin Alder</p>
    <p class="person-role">Owner</p>
  </div>

  <div class="divider"></div>

  <ul class="contacts">
    <li>
      <svg viewBox="0 0 16 16" aria-hidden="true"><path d="M2 5c0-2 2-3 6-3s6 1 6 3v1h-3V5H5v1H2z M4 7h8l2 7H2z"/></svg>
      051-870 224 316
    </li>
    <li>
      <svg viewBox="0 0 16 16" aria-hidden="true"><path d="M4 1h8v14H4z M5.5 2.5v9h5v-9z M7 13h2v1H7z"/></svg>
      051-870 224 316
    </li>
    <li>
      <svg viewBox="0 0 16 16" aria-hidden="true"><path d="M1 4h14v9H1z M2 5l6 4 6-4v-.5H2z" fill-rule="evenodd"/></svg>
      hello@veldmark.net
    </li>
  </ul>

  <address class="address" style="font-style:normal">
    88, Refinery Road East<br>
    79760, Basin County
  </address>

  <svg class="stripes" viewBox="0 0 560 40" aria-hidden="true">
    <polygon points="0,26 330,26 326,30 0,30" fill="var(--red)"/>
    <polygon points="0,33 330,33 346,12 560,12 560,40 0,40" fill="var(--cyan)"/>
  </svg>
  <p class="website">www.veldmark.net</p>
</section>

</body>
</html>
```